design a construction company business card

Design business card around our logo. Card must have all the typical info: name, title, address, phone, email, business name, etc. Somewhere on the card I would like to see our motto "Solid foundations... Lasting relationships." Consider adding a splash of bright orange to the card to complement the blues and silvers/grays in the logo. We are open to metallic inks, textures, etc. We would like to see options on both light and dark backgrounds. The font in the logo is Euro Technic Extended Regular.

```html
<!DOCTYPE html>
<html lang="en">
<head>
<meta charset="utf-8">
<title>Halden Builders – Business Card</title>
<link rel="stylesheet" href="https://fonts.googleapis.com/css2?family=Michroma&family=Montserrat:wght@400;500&display=swap">
<style>
  :root {
    --backdrop: #e9e8e5;
    --card-dark: #1f2f9e;
    --card-light: #f6f6f4;
    --brand-blue: #2446b5;
    --silver: #d9dbe0;
    --ink: #2b2b2b;
    --ink-soft: #4a4a4a;
    --decor-top: #2a3aa8;
    --decor-bottom: #3446b4;
  }
  * { box-sizing: border-box; margin: 0; padding: 0; }
  html, body { width: 1200px; height: 694px; overflow: hidden; }
  body {
    background: var(--backdrop);
    font-family: "Montserrat", sans-serif;
    position: relative;
  }
  .card {
    position: absolute;
    top: 87px;
    width: 297px;
    height: 520px;
    box-shadow: 0 6px 18px rgba(0,0,0,0.14);
  }
  .card--front {
    left: 268px;
    background: var(--card-dark);
  }
  .card--back {
    left: 635px;
    background: var(--card-light);
  }
  .front-name {
    position: absolute;
    top: 62px;
    left: 0;
    width: 100%;
    text-align: center;
    font-family: "Michroma", sans-serif;
    font-size: 27px;
    letter-spacing: 2px;
    color: var(--silver);
  }
  .front-decor {
    position: absolute;
    left: 40px;
    right: 0;
    bottom: 0;
    height: 270px;
    background: linear-gradient(180deg, var(--decor-top), var(--decor-bottom));
    opacity: 0.9;
  }
  .back-brand {
    position: absolute;
    top: 80px;
    left: 0;
    width: 100%;
    display: flex;
    justify-content: center;
    align-items: center;
    gap: 8px;
  }
  .back-brand__square {
    flex: none;
    width: 12px;
    height: 12px;
    background: var(--brand-blue);
  }
  .back-brand__name {
    font-family: "Michroma", sans-serif;
    font-size: 12.5px;
    letter-spacing: 0.5px;
    white-space: nowrap;
    color: var(--brand-blue);
  }
  .contact {
    position: absolute;
    left: 30px;
    top: 230px;
    right: 14px;
    color: var(--ink);
  }
  .contact__person {
    font-family: "Michroma", sans-serif;
    font-size: 15px;
    letter-spacing: 2px;
    color: var(--brand-blue);
  }
  .contact__title {
    font-size: 10.5px;
    letter-spacing: 0.5px;
    color: var(--ink-soft);
    margin-top: 4px;
    text-transform: uppercase;
  }
  .contact__lines {
    margin-top: 30px;
    font-size: 11.5px;
    line-height: 1.35;
  }
  .contact__address {
    margin-top: 14px;
    font-size: 11.5px;
    line-height: 1.35;
  }
  .motto {
    margin-top: 18px;
    font-size: 10px;
    white-space: nowrap;
    color: var(--ink);
  }
</style>
</head>
<body>
  <section class="card card--front" aria-label="Business card front">
    <div class="front-name">HALDEN</div>
    <div class="front-decor" role="img" aria-label="Faint line decoration of the company skyline symbol"></div>
  </section>

  <section class="card card--back" aria-label="Business card back">
    <div class="back-brand">
      <span class="back-brand__square"></span>
      <span class="back-brand__name">HALDEN BUILDERS, INC.</span>
    </div>
    <div class="contact">
      <p class="contact__person">DANIEL REYES</p>
      <p class="contact__title">CEO / Founder</p>
      <p class="contact__lines">
        555 210 4821<br>
        info@haldenbuild.com<br>
        www.haldenbuild.com
      </p>
      <p class="contact__address">
        318 Spruce Hollow Way<br>
        Bozeman, Montana 59715
      </p>
      <p class="motto">Solid foundations... Lasting relationships.</p>
    </div>
  </section>
</body>
</html>
```